Commercial Cleaning Company Website Design

We are working with Harbor Tidy Team. They are a commercial cleaning company that needs a new website design.

Some sites to use for inspiration:

https://www.plenvask.com
https://gleam-panecare.com
https://tidwellhelpers.net
https://quietnesthouse.com
https://www.thedustingbureau.com
https://www.pennytidy.com

Thank you for taking the time to consider designing a website for us. We are web developers based in Stockton and Los Angeles, CA, USA. Most of our projects go through the same process. Understanding this process may help you win a project with us. We custom-code all of our websites in-house. We don’t have any requirements as to what tools you use for your design, but we prefer Figma files. For any design that we label as four-stars, we send it to the client for review. The client picks the final design they want us to use. Once we complete this process, we will continue to show additional clients all the four-star sites and purchase them later. Your designs will have multiple chances to sell. For better chances of success, we ask that you follow these guidelines.

IMAGES:
If you use any images or icons in the design, we ask that you have a link to the asset so we can purchase the image/icon. Most of the designs we submit do not have the customer’s images on them unless they have some great images. Be creative; show us the feeling you are trying to portray with your image choices. Use any royalty-free site you choose. We subscribe to Adobe and mainly use their images, but we can purchase images outside of Adobe.

PLEASE NOTE: we will not submit designs to clients with watermarks on the images.

FONTS:
We ask that you identify the fonts used in the design. This can be done in a message if you want. We typically use Google Fonts and Adobe Fonts.

CONTENT:
We're always open to different content and ideas. We often submit designs with stock images so the client can see our vision. We typically take pictures after the website launch to use their images with our vision. Lorem Ipsum is fine for paragraphs, but we ask that you write the headers in correct English. We want to be able to show the vision and identify the sections of the website.

INSPIRATION:
We typically add a couple of links in the brief of websites we like to help you get started in your design.

REVISIONS:
We do not often ask for revisions of the designs unless we see something in the design that may not appeal to the client. If there are slight changes that we want to make, we do that in the development process.

FEEDBACK:
We rarely give feedback on designs during the design process. We are working on many website projects and do not have the time to provide feedback. We usually respond if your request is well thought out and asks specific questions, but a note asking “feedback, please” usually goes unanswered.

```html
<!DOCTYPE html>
<html lang="en">
<head>
<meta charset="utf-8">
<title>Harbor Tidy Team — Commercial Cleaning</title>
<link href="https://fonts.googleapis.com/css2?family=Montserrat:wght@600;700;800&family=Poppins:ital,wght@0,400;0,500;0,600;1,400;1,500&display=swap" rel="stylesheet">
<style>
:root{
  --blue:#1f3ea6;
  --blue-deep:#17339a;
  --blue-soft:#c9d3f2;
  --red:#e8171c;
  --red-soft:#f4a3a0;
  --ink:#222;
  --muted:#555;
  --line:#e6e6e6;
  --white:#fff;
}
*{box-sizing:border-box;margin:0;padding:0}
html,body{width:1200px;height:5263px;overflow:hidden}
body{position:relative;background:var(--white);font-family:"Poppins",sans-serif;color:var(--ink)}
.abs{position:absolute}
.heading{font-family:"Montserrat",sans-serif;font-weight:800;color:var(--blue);letter-spacing:8px;text-transform:uppercase}
.eyebrow{font-family:"Montserrat",sans-serif;font-weight:700;color:var(--red);letter-spacing:4px;text-transform:uppercase;font-size:19px;display:flex;align-items:center;gap:16px}
.eyebrow::before,.eyebrow::after{content:"";width:60px;height:2px;background:var(--red)}
.eyebrow.left::before{display:none}
.center{left:0;width:1200px;text-align:center;justify-content:center}
.btn{display:inline-flex;align-items:center;justify-content:center;border-radius:40px;color:var(--white);font-weight:500;text-transform:uppercase}
.btn-red{background:var(--red)}
.btn-blue{background:var(--blue)}
.para{font-size:14px;line-height:25.5px;color:var(--muted)}
.photo{border-radius:0}

/* header */
.brand{font-family:"Montserrat",sans-serif;font-weight:800;color:var(--blue);font-size:22px;letter-spacing:4px;text-transform:uppercase;display:flex;align-items:center;gap:12px}
.brand .mark{width:26px;height:26px;border-radius:50%;background:var(--red)}
.nav{display:flex;gap:36px;font-size:13px;color:var(--ink)}
.phone{font-size:13px;color:var(--blue);display:flex;align-items:center;gap:6px}

/* service cards */
.svc{width:316px;text-align:center}
.svc .img{height:266px;border-radius:10px;position:relative}
.svc .icon{position:absolute;left:50%;bottom:-44px;transform:translateX(-50%);width:92px;height:92px;border-radius:50%;border:6px solid var(--white);display:flex;align-items:center;justify-content:center}
.svc h3{font-size:19px;font-weight:600;color:var(--red);text-transform:uppercase;line-height:24px;margin-top:72px}
.svc .bar{width:38px;height:2px;background:var(--red);margin:8px auto 14px}
.svc p{font-size:13px;line-height:21px;color:var(--muted)}
.svc.feature{border:1px solid var(--line);border-radius:12px;box-shadow:0 6px 18px rgba(0,0,0,.06);padding-bottom:24px}

/* why cards */
.why{width:238px;height:136px;border:1px solid var(--line);box-shadow:0 4px 14px rgba(0,0,0,.06);text-align:center;padding-top:40px;background:var(--white)}
.why h4{font-size:15px;font-weight:500;color:var(--blue)}
.why .bar{width:30px;height:2px;background:var(--red);margin:5px auto 8px}
.why p{font-size:12.5px;line-height:20px;color:var(--muted)}
.why-icon{width:56px;height:56px;border-radius:50%;border:4px solid var(--white);box-shadow:0 2px 6px rgba(0,0,0,.15);display:flex;align-items:center;justify-content:center}

/* reviews */
.review{width:328px;height:216px;border-radius:12px;padding:76px 24px 0 22px;color:var(--white);font-style:italic;font-size:12.5px;line-height:21px}
.review::after{content:"";position:absolute;left:50px;bottom:-14px;border:14px solid transparent;border-bottom:0;border-top-color:inherit}
.quote{position:absolute;left:20px;top:6px;font-family:"Montserrat",sans-serif;font-size:110px;font-weight:800;line-height:1;opacity:.35;font-style:normal}
.reviewer{display:flex;align-items:center;gap:18px}
.avatar{width:78px;height:78px;border-radius:50%;background:linear-gradient(135deg,#d9b89d,#7b5844);border:4px solid var(--white);box-shadow:0 2px 8px rgba(0,0,0,.2)}
.reviewer b{display:block;font-size:13px;font-weight:600}
.stars{color:#f2b01e;font-size:12px;letter-spacing:1px}

/* contact form */
.field{height:52px;border:1px solid var(--line);box-shadow:0 2px 10px rgba(0,0,0,.05);padding:16px 22px;font-size:14px;color:#888;background:var(--white)}

/* footer */
.footer{left:0;top:4895px;width:1200px;height:368px;background:var(--blue)}
.footer *{color:var(--white)}
.fcol h5{font-size:14px;font-weight:500;letter-spacing:.5px;margin-bottom:34px}
.flinks li{list-style:none;font-size:11.5px;line-height:24px;display:flex;align-items:center;gap:6px}
.flinks li::before{content:"";width:8px;height:8px;border:1.5px solid var(--white);border-radius:50%}
.fdiv{width:2px;height:60px;background:rgba(255,255,255,.7)}
.cinfo{display:flex;gap:14px;align-items:center;font-size:11px;line-height:13px;margin-bottom:16px}
.cinfo .ic{width:28px;height:28px;border:1.5px solid var(--white);border-radius:4px;display:flex;align-items:center;justify-content:center}
.social{width:26px;height:26px;background:var(--white);border-radius:3px}
</style>
</head>
<body>

<!-- Header -->
<div class="abs brand" style="left:66px;top:48px"><span class="mark"></span>Harbor Tidy Team</div>
<div class="abs phone" style="left:880px;top:33px">
  <svg width="22" height="22" viewBox="0 0 24 24"><circle cx="12" cy="12" r="11" fill="#e8171c"/><path d="M8 6l2 3-1 1.5c.8 1.8 2 3 3.5 3.5L14 13l3 2-1 2.5c-4 0-8.5-4.5-8.5-8.5z" fill="#fff"/></svg>
  0100 555 210
</div>
<div class="abs btn btn-blue" style="left:1036px;top:31px;width:98px;height:26px;font-size:11px">Book Now</div>
<nav class="abs nav" style="left:610px;top:70px"><span>Home</span><span>About</span><span>Services</span><span>Areas Served</span><span>Careers</span><span>Contact Us</span></nav>
<div class="abs" style="left:66px;top:107px;width:1070px;height:2px;background:var(--blue)"></div>

<!-- Hero -->
<div class="abs" style="left:68px;top:234px;font-size:24px;font-weight:500">Welcome To</div>
<div class="abs heading" style="left:66px;top:278px;font-size:72px;letter-spacing:10px;line-height:1">Harbor</div>
<div class="abs heading" style="left:68px;top:366px;font-size:38px;letter-spacing:8px">Tidy Team</div>
<div class="abs" style="left:78px;top:436px;font-size:21px;color:#333">Most Trusted Commercial Cleaning</div>
<div class="abs btn btn-red" style="left:68px;top:510px;width:222px;height:62px;font-size:22px">Book Now</div>
<svg class="abs" style="left:570px;top:180px" width="600" height="570" viewBox="0 0 600 570">
  <path d="M260 70 C400 60 560 120 580 260 C600 400 520 520 380 545 C300 560 230 520 260 460 Z" fill="var(--blue-soft)"/>
  <path d="M70 220 C40 300 30 380 80 450 L140 470 L150 240 Z" fill="var(--red-soft)" opacity=".35"/>
  <path d="M200 40 C330 10 460 60 500 170 C540 290 520 440 440 520 C360 590 230 560 170 470 C110 380 30 300 60 190 C80 110 130 55 200 40 Z" fill="url(#heroG)" role="img" aria-label="Worker in safety vest pushing a floor scrubbing machine"/>
  <defs><linearGradient id="heroG" x1="0" y1="0" x2="1" y2="1"><stop offset="0" stop-color="#b7b9b3"/><stop offset=".55" stop-color="#8f8d84"/><stop offset="1" stop-color="#d8a52a"/></linearGradient></defs>
</svg>

<!-- Services -->
<div class="abs heading center" style="top:928px;font-size:50px">Our Services</div>
<div class="abs eyebrow center" style="top:993px">What We Do</div>
<p class="abs para center" style="top:1052px;padding:0 160px;font-size:14px;line-height:31px">Lorem ipsum dolor sit amet, conse ctetur adipiscing elit, sed do eiu smod tempor incididunt ut labore et dolore magna aliqua. Quis ipsum suspendisse ultrices gravida. Risus commodo viverra maecenas accumsan lacus vel facilisis.</p>
<div class="abs" style="left:1028px;top:1138px;width:46px;height:46px;border-radius:50%;background:var(--red);color:#fff;display:flex;align-items:center;justify-content:center;font-size:18px">‹</div>
<div class="abs" style="left:1082px;top:1138px;width:46px;height:46px;border-radius:50%;background:var(--blue);color:#fff;display:flex;align-items:center;justify-content:center;font-size:18px">›</div>

<div class="abs svc" style="left:96px;top:1220px">
  <div class="img" role="img" aria-label="Window cleaners abseiling down a glass tower" style="background:linear-gradient(160deg,#5f8fc9,#1d4f91)"><div class="icon" style="background:var(--blue)"></div></div>
  <h3>Window Cleaning</h3><div class="bar"></div>
  <p>Lorem ipsum dolor sit amet, conse<br>ctetur adipiscing elit, sed do eiu</p>
</div>
<div class="abs svc feature" style="left:438px;top:1220px">
  <div class="img" role="img" aria-label="Cleaner vacuuming an office floor" style="background:linear-gradient(160deg,#d9d9d4,#8a8880);border-radius:10px 10px 0 0"><div class="icon" style="background:var(--red)"></div></div>
  <h3 style="margin-top:68px">Commercial<br>Pressure Washing</h3><div class="bar"></div>
  <p>Lorem ipsum dolor sit amet, conse<br>ctetur adipiscing elit, sed do eiu</p>
  <div class="btn btn-red" style="width:134px;height:40px;font-size:12px;font-weight:600;margin-top:16px">Read More</div>
</div>
<div class="abs svc" style="left:784px;top:1220px">
  <div class="img" role="img" aria-label="Cleaner in protective suit with cleaning cart in a clinic" style="background:linear-gradient(160deg,#e4e6e8,#9fa4aa)"><div class="icon" style="background:var(--blue)"></div></div>
  <h3>Medical Cleaning</h3><div class="bar"></div>
  <p>Lorem ipsum dolor sit amet, conse<br>ctetur adipiscing elit, sed do eiu</p>
</div>

<!-- About -->
<svg class="abs" style="left:36px;top:1880px" width="470" height="460" viewBox="0 0 470 460">
  <circle cx="270" cy="250" r="210" fill="var(--red-soft)"/>
  <circle cx="270" cy="120" r="95" fill="var(--blue-soft)" opacity=".6"/>
  <path d="M110 40 C220 0 340 40 400 140 C450 230 430 350 340 400 C260 440 150 420 90 350 C20 270 0 80 110 40 Z" fill="url(#aboutG)" role="img" aria-label="Woman in yellow gloves cleaning a window"/>
  <defs><linearGradient id="aboutG" x1="0" y1="0" x2="1" y2="1"><stop offset="0" stop-color="#c6cfd4"/><stop offset=".6" stop-color="#eef0ef"/><stop offset="1" stop-color="#aab6bb"/></linearGradient></defs>
</svg>
<div class="abs heading" style="left:604px;top:1900px;font-size:50px">About Us</div>
<div class="abs eyebrow left" style="left:606px;top:1970px">Who We Are</div>
<p class="abs para" style="left:600px;top:2016px;width:462px;text-align:justify">Lorem ipsum dolor sit amet, consectetur adipiscing elit, sed do eiusm od tempor incididunt ut labore et dolore magna aliqua. Quis ipsum suspendisse ultrices gravida. Risus commodo viverra maecenas acc umsan lacus vel facilisis. Lorem ipsum dolor sit amet, consectetur adipiscing elit, sed do eiusmod tempor incididunt ut labore et dolore magna aliqua. Lorem ipsum dolor sit amet, consectetur adipiscing elit, sed do eiusmod tempor incididunt ut labore et dolore magna aliqua. Quis ipsum suspendisse ultrices gravida. Risus commodo viverra maecenas accumsan lacus vel facilisis.</p>
<div class="abs btn btn-blue" style="left:600px;top:2276px;width:156px;height:42px;font-size:14px;text-transform:uppercase">Know More</div>

<!-- Why choose -->
<div class="abs heading center" style="top:2500px;font-size:50px">Why Choose Us</div>
<div class="abs eyebrow center" style="top:2568px">Harbor Tidy Team</div>
<div class="abs why" style="left:88px;top:2680px"><h4>Trust</h4><div class="bar"></div><p>Lorem ipsum dolor sit amet,<br>consectetur adipiscing elit.</p></div>
<div class="abs why" style="left:350px;top:2680px"><h4>Affordability</h4><div class="bar"></div><p>Lorem ipsum dolor sit amet,<br>consectetur adipiscing.</p></div>
<div class="abs why" style="left:612px;top:2680px"><h4>Quality</h4><div class="bar"></div><p>Lorem ipsum dolor sit amet,<br>consectetur adipiscing elit.</p></div>
<div class="abs why" style="left:873px;top:2680px"><h4>Locally Owned</h4><div class="bar"></div><p>Lorem ipsum dolor sit amet,<br>consectetur adipiscing.</p></div>
<div class="abs why-icon" style="left:180px;top:2656px;background:var(--blue)"><svg width="22" height="22" viewBox="0 0 24 24"><path d="M4 13l5 5L20 6" stroke="#fff" stroke-width="2.5" fill="none"/></svg></div>
<div class="abs why-icon" style="left:441px;top:2656px;background:var(--red)"><svg width="22" height="22"><text x="11" y="17" text-anchor="middle" font-size="16" font-family="Poppins" fill="#fff">$</text></svg></div>
<div class="abs why-icon" style="left:703px;top:2656px;background:var(--blue)"><svg width="22" height="22"><circle cx="11" cy="11" r="8" stroke="#fff" stroke-width="2" fill="none"/><circle cx="11" cy="11" r="3.5" fill="#fff"/></svg></div>
<div class="abs why-icon" style="left:964px;top:2656px;background:var(--red)"><svg width="22" height="22" viewBox="0 0 24 24"><path d="M12 2a7 7 0 0 0-7 7c0 5 7 13 7 13s7-8 7-13a7 7 0 0 0-7-7z" fill="#fff"/><circle cx="12" cy="9" r="2.5" fill="#e8171c"/></svg></div>

<!-- How we work -->
<div class="abs heading" style="left:70px;top:2930px;font-size:52px;line-height:60px">How We<br>Work</div>
<div class="abs" style="left:72px;top:3062px;width:60px;height:4px;background:var(--red)"></div>
<p class="abs para" style="left:70px;top:3106px;width:272px;text-align:justify;font-size:13px">Lorem ipsum dolor sit amet, consectetur adipiscing elit, sed do eiusm od tempor incididunt ut labore et dolore magna aliqua. Quis ipsum suspendisse ultrices gravida. Risus commodo</p>
<div class="abs btn btn-red" style="left:68px;top:3273px;width:186px;height:62px;font-size:18px;text-transform:none">BOOK NOW</div>
<div class="abs" role="img" aria-label="Cleaners vacuuming and wiping a bright meeting room" style="left:383px;top:2900px;width:744px;height:476px;background:linear-gradient(120deg,#e8e8e6,#b8b7b2 60%,#2c2c2c)"></div>
<div class="abs" style="left:709px;top:3110px;width:56px;height:56px;border-radius:50%;background:var(--white);display:flex;align-items:center;justify-content:center"><svg width="20" height="20"><path d="M6 3l12 7-12 7z" fill="#e8171c"/></svg></div>

<!-- Reviews -->
<div class="abs heading center" style="top:3534px;font-size:50px">Client Reviews</div>
<div class="abs eyebrow center" style="top:3602px">Testimonials</div>
<div class="abs review" style="left:75px;top:3705px;background:var(--blue-deep);border-color:var(--blue-deep)"><span class="quote">“</span>Lorem ipsum dolor sit amet, consectetur adipiscing elit, sed do eiusmod tempor incididunt ut labore et dolore magna aliqua. Quis ipsum suspendisse ultrices gravida.</div>
<div class="abs review" style="left:440px;top:3705px;background:var(--red);border-color:var(--red)"><span class="quote">“</span>Lorem ipsum dolor sit amet, consectetur adipiscing elit, sed do eiusmod tempor incididunt ut labore et dolore magna aliqua. Quis ipsum suspendisse ultrices gravida.</div>
<div class="abs review" style="left:796px;top:3705px;background:var(--blue-deep);border-color:var(--blue-deep)"><span class="quote">“</span>Lorem ipsum dolor sit amet, consectetur adipiscing elit, sed do eiusmod tempor incididunt ut labore et dolore magna aliqua. Quis ipsum suspendisse ultrices gravida.</div>
<div class="abs reviewer" style="left:94px;top:3936px"><div class="avatar" role="img" aria-label="Client portrait"></div><div><b>Marla Quinn</b><span class="stars">★★★★★</span></div></div>
<div class="abs reviewer" style="left:458px;top:3936px"><div class="avatar" role="img" aria-label="Client portrait"></div><div><b>Marla Quinn</b><span class="stars">★★★★★</span></div></div>
<div class="abs reviewer" style="left:815px;top:3936px"><div class="avatar" role="img" aria-label="Client portrait"></div><div><b>Marla Quinn</b><span class="stars">★★★★★</span></div></div>
<div class="abs" style="left:566px;top:4146px;display:flex;gap:8px">
  <span style="width:9px;height:9px;border-radius:50%;background:var(--blue)"></span>
  <span style="width:9px;height:9px;border-radius:50%;background:var(--blue-soft)"></span>
  <span style="width:9px;height:9px;border-radius:50%;background:var(--blue-soft)"></span>
  <span style="width:9px;height:9px;border-radius:50%;background:var(--blue-soft)"></span>
</div>

<!-- Contact -->
<div class="abs heading" style="left:578px;top:4220px;width:552px;text-align:center;font-size:50px">Contact Us</div>
<div class="abs eyebrow" style="left:578px;top:4286px;width:552px;justify-content:center">Harbor Tidy Team</div>
<svg class="abs" style="left:36px;top:4266px" width="480" height="470" viewBox="0 0 480 470">
  <circle cx="285" cy="270" r="185" fill="var(--blue-soft)"/>
  <path d="M60 300 C40 380 90 450 170 460 L120 280 Z" fill="var(--red-soft)" opacity=".4"/>
  <path d="M190 10 C300 0 420 70 450 180 C480 300 400 420 280 440 C170 460 70 400 50 290 C30 170 80 20 190 10 Z" fill="url(#contactG)" role="img" aria-label="Gloved hand using a squeegee on a window"/>
  <defs><linearGradient id="contactG" x1="0" y1="0" x2="1" y2="1"><stop offset="0" stop-color="#3b4e5c"/><stop offset=".5" stop-color="#8fa1aa"/><stop offset="1" stop-color="#2f3a44"/></linearGradient></defs>
</svg>
<div class="abs field" style="left:578px;top:4346px;width:264px">First Name:</div>
<div class="abs field" style="left:866px;top:4346px;width:264px">Last Name:</div>
<div class="abs field" style="left:578px;top:4422px;width:264px">Phone:</div>
<div class="abs field" style="left:866px;top:4422px;width:264px">Email:</div>
<div class="abs field" style="left:578px;top:4502px;width:552px;height:168px">Message:</div>
<div class="abs btn btn-red" style="left:580px;top:4710px;width:186px;height:62px;font-size:18px">Submit Now</div>

<!-- Footer -->
<footer class="abs footer">
  <div class="abs brand" style="left:66px;top:120px;font-size:22px"><span class="mark"></span>Harbor Tidy Team</div>
  <div class="abs" style="left:134px;top:238px;display:flex;gap:8px"><span class="social"></span><span class="social"></span><span class="social"></span><span class="social"></span></div>
  <div class="abs fdiv" style="left:410px;top:112px"></div>
  <div class="abs fcol" style="left:430px;top:132px"><h5>QUICK LINKS</h5>
    <ul class="flinks"><li>Home</li><li>About Us</li><li>Services</li><li>Reviews</li><li>Contact</li></ul></div>
  <div class="abs fdiv" style="left:600px;top:112px"></div>
  <div class="abs fcol" style="left:630px;top:132px"><h5>CONTACT US</h5>
    <div class="cinfo"><span class="ic"><svg width="14" height="14" viewBox="0 0 24 24"><path d="M6 3l4 5-2 2c1.5 3 3.5 5 6 6l2-2 5 4-2 3C11 21 3 13 3 5z" fill="#fff"/></svg></span><span>CALL US<br>0100 555 2148</span></div>
    <div class="cinfo"><span class="ic"><svg width="14" height="12"><rect x="1" y="1" width="12" height="10" stroke="#fff" fill="none"/><path d="M1 1l6 5 6-5" stroke="#fff" fill="none"/></svg></span><span>EMAIL US<br>hello@harbortidyteam.com</span></div>
    <div class="cinfo"><span class="ic"><svg width="12" height="14" viewBox="0 0 24 24"><path d="M12 2a7 7 0 0 0-7 7c0 5 7 13 7 13s7-8 7-13a7 7 0 0 0-7-7z" fill="#fff"/></svg></span><span>Address line Dummy Here<br>Address line Here</span></div>
  </div>
  <div class="abs fdiv" style="left:872px;top:112px"></div>
  <div class="abs fcol" style="left:902px;top:136px"><h5 style="margin-bottom:22px">NEWSLETTER SIGN UP</h5>
    <p style="font-size:11.5px;line-height:16px;width:200px">Subscribe our newsletter to get the latest news.</p>
    <div style="margin-top:22px;width:192px;height:32px;border:1.5px solid #fff;border-radius:20px;display:flex;align-items:center;justify-content:space-between;padding:0 4px 0 14px;font-size:9.5px">Enter Email Address<span style="width:22px;height:22px;border:1.5px solid #fff;border-radius:50%;display:flex;align-items:center;justify-content:center;font-size:12px">→</span></div>
  </div>
  <div class="abs" style="left:0;top:342px;width:1200px;text-align:center;font-size:10.5px">Copyright © 2025 All Rights Reserved By Company name</div>
</footer>

</body>
</html>
```